WEBSITE DESIGN, VELTRA paint and panel

We are in need of a website for Veltra Paint & Panel based in Brisbane, Australia. We are a boutique Automotive Paint & Panel Company that provides services to all makes and models of vehicles. We have attached a logo that is still in draft stage but gives you an idea of the colour scheme and fonts and overall impact we are looking for. We are after a white background so this is clean and crisp whilst being sleek, modern and professional. The website must represent our slogan of Glowing finish on the Gleaming frame. The website must therefore be visually effective as our product is to get colour and placement on vehicle body's correct so the website must have this impact on our clients. We are after a widescreen webpage that is simple and logical to navigate. The final design should give clients the confidence that we can deliver on our promise.
Updates

Target Market(s)

Vehicle Owners who have a need for panel repairs and people who want to reinvigorate their car with a new coat of paint.

Industry/Entity Type

Car Repair

Coding

Coded - Design and coding required

Number of Pages Required

5+ page

Font styles to use
Sans Serif

Colors
ffffff
ffc214
000000

Requirements
Must have
• Page 1 - Home Page
• Page 2 - Our Process
• Page 3 - Private Customers
• Page 4 - Fleet & Corporate
• Page 5 - Insurance
• Page 6 - Get a Quote
• Page 7 - Connect (Contacts Page)
• Same font and colour scheme as the logo.
Should not have
• A typical mechanical/paint and panel layout which looks like a template website.

```html
<!DOCTYPE html>
<html lang="en">
<head>
<meta charset="utf-8">
<title>Veltra Paint &amp; Panel</title>
<link href="https://fonts.googleapis.com/css2?family=Montserrat:wght@600;700;800&family=Open+Sans:wght@400;600;700&display=swap" rel="stylesheet">
<style>
:root{
  --yellow:#ffc214;
  --black:#000000;
  --ink:#1c1c1c;
  --text:#6b6b6b;
  --white:#ffffff;
  --band:#f1f1f1;
  --line:#e2e2e2;
  --hero-a:#cfd2d4;
  --hero-b:#6e7377;
}
*{box-sizing:border-box;margin:0;padding:0}
html,body{width:828px;height:1200px;overflow:hidden;background:var(--white)}
body{font-family:"Open Sans",Arial,sans-serif;color:var(--text);font-size:7px;line-height:1.55}
.page{width:828px;height:1200px;position:relative}
.wrap{width:620px;margin:0 auto;position:relative}
h2,h3,.nav a,.btn,.hero-title{font-family:"Montserrat",Arial,sans-serif}

/* header */
.site-header{height:82px;position:relative}
.brand{position:absolute;left:24px;top:14px;display:flex;align-items:center;gap:8px}
.brand-mark{width:18px;height:18px;background:var(--yellow)}
.brand-name{font-family:"Montserrat",Arial,sans-serif;font-weight:800;font-size:17px;color:var(--ink);letter-spacing:.5px;line-height:1.1;width:130px}
.contact{position:absolute;right:30px;top:6px;display:flex;gap:26px}
.contact-item{display:flex;align-items:center;gap:6px;font-size:6.5px;color:var(--ink);line-height:1.3}
.contact-item strong{display:block;font-weight:700}
.contact-icon{width:18px;height:18px;border-radius:50%;background:var(--ink);display:flex;align-items:center;justify-content:center}
.nav{position:absolute;left:222px;right:0;top:44px;height:36px;background:var(--black);display:flex;align-items:stretch;padding-left:10px}
.nav a{color:var(--white);text-decoration:none;font-size:6.5px;font-weight:600;letter-spacing:.4px;padding:0 11px;display:flex;align-items:center}
.nav a.active,.nav a.mark{background:var(--yellow);color:var(--black)}

/* hero */
.hero{height:358px;position:relative;background:linear-gradient(120deg,var(--hero-a) 0%,#a9adb0 40%,var(--hero-b) 100%);overflow:hidden}
.hero-title{position:absolute;left:0;right:0;top:148px;text-align:center;color:var(--white);font-weight:800;font-size:34px;line-height:1.08;letter-spacing:.5px}
.hero-title em{font-style:normal;color:var(--yellow)}
.hero-arrow{position:absolute;top:168px;width:24px;height:24px;border-radius:50%;background:rgba(0,0,0,.45);display:flex;align-items:center;justify-content:center}
.hero-arrow.prev{left:22px}.hero-arrow.next{right:22px}
.dots{position:absolute;bottom:14px;left:0;right:0;display:flex;justify-content:center;gap:6px}
.dots span{width:7px;height:7px;border-radius:50%;background:rgba(255,255,255,.6)}
.dots span.on{background:var(--yellow)}

/* services */
.services{padding-top:22px;height:262px}
.service-grid{display:grid;grid-template-columns:repeat(4,1fr);gap:18px}
.service-photo{height:80px;background:linear-gradient(135deg,#d9dcdf,#8a8f94)}
.service-photo.s2{background:linear-gradient(135deg,#e7d9a8,#9d9a8e)}
.service-photo.s3{background:linear-gradient(135deg,#c3c8cc,#4c5459)}
.service-photo.s4{background:linear-gradient(135deg,#cfd3d6,#707a80)}
.service h3{font-size:8.5px;font-weight:700;color:var(--ink);margin:12px 0 5px}
.service p{font-size:6.2px;margin-bottom:10px}
.btn{display:inline-block;background:var(--yellow);color:var(--black);font-size:6px;font-weight:700;padding:5px 10px;letter-spacing:.4px}

/* about */
.about{height:250px;padding-top:22px;border-top:1px solid var(--line)}
.about .wrap{display:flex;gap:24px}
.about-text{flex:1.2}
.stories{flex:1}
.about h2,.stories h2,.works h2{font-size:10px;font-weight:700;color:var(--ink);margin-bottom:10px;letter-spacing:.3px}
.about-text p{font-size:6.4px;margin-bottom:8px}
.story{display:flex;gap:10px}
.story-photo{width:100px;height:80px;flex:none;background:linear-gradient(135deg,#c9b8a4,#5d5a58)}
.story p{font-size:6.4px}

/* works */
.works{background:var(--band);height:150px;padding-top:18px}
.works .wrap{display:flex;gap:22px}
.works-text{flex:1}
.works-text p{font-size:6.4px;margin-bottom:6px}
.compare{display:flex;gap:16px}
.compare figure{width:150px;text-align:center}
.car-photo{height:80px;background:linear-gradient(160deg,#eef2f5 0%,#6d8fb4 55%,#2b4a70 100%)}
.car-photo.after{background:linear-gradient(160deg,#f4f6f8 0%,#4f7fb8 55%,#1c3f6c 100%)}
.compare figcaption{margin-top:5px;font-size:6px;font-weight:700;color:var(--ink);letter-spacing:.5px}

/* makes */
.makes{height:50px;display:flex;align-items:center}
.makes .wrap{display:flex;align-items:center;gap:18px}
.makes h3{font-size:7px;font-weight:700;color:var(--ink);line-height:1.2;width:58px}
.make-badge{width:34px;height:18px;border-radius:9px;background:#c9c9c9}

/* footer */
.site-footer{height:50px;background:var(--black);color:#9a9a9a}
.site-footer .wrap{display:flex;justify-content:space-between;align-items:center;height:50px}
.footer-links{font-size:5.5px;letter-spacing:.3px;line-height:1.8}
.footer-links span{color:#d0d0d0;margin-right:9px}
.social{display:flex;gap:6px}
.social span{width:14px;height:14px;border-radius:50%;background:var(--yellow)}
</style>
</head>
<body>
<div class="page">

  <header class="site-header">
    <div class="brand">
      <span class="brand-mark"></span>
      <span class="brand-name">VELTRA paint and panel</span>
    </div>
    <div class="contact">
      <div class="contact-item">
        <span class="contact-icon"><svg width="9" height="9" viewBox="0 0 24 24"><path fill="#ffc214" d="M6.6 10.8a15.1 15.1 0 0 0 6.6 6.6l2.2-2.2a1 1 0 0 1 1-.25 11.4 11.4 0 0 0 3.6.57 1 1 0 0 1 1 1V20a1 1 0 0 1-1 1A17 17 0 0 1 3 4a1 1 0 0 1 1-1h3.5a1 1 0 0 1 1 1c0 1.25.2 2.45.57 3.57a1 1 0 0 1-.25 1z"/></svg></span>
        <span><strong>Call Us</strong>1300 555 018</span>
      </div>
      <div class="contact-item">
        <span class="contact-icon"><svg width="9" height="9" viewBox="0 0 24 24"><path fill="#ffc214" d="M2 5h20v14H2zm2 2v.5l8 5 8-5V7l-8 5z"/></svg></span>
        <span><strong>Email Us</strong>hello@veltrapanel.com.au</span>
      </div>
    </div>
    <nav class="nav">
      <a class="active">HOME</a>
      <a>OUR PROCESS</a>
      <a>PRIVATE CUSTOMERS</a>
      <a>FLEET &amp; CORPORATE</a>
      <a class="mark">INSURANCE</a>
      <a>GET A QUOTE</a>
      <a>CONNECT</a>
    </nav>
  </header>

  <section class="hero" role="img" aria-label="Painter in protective suit spraying a car panel in a paint booth">
    <h1 class="hero-title">GLOWING FINISH<br>ON THE <em>GLEAMING</em> FRAME</h1>
    <span class="hero-arrow prev"><svg width="8" height="8" viewBox="0 0 10 10"><path d="M7 1 3 5l4 4" stroke="#fff" stroke-width="1.6" fill="none"/></svg></span>
    <span class="hero-arrow next"><svg width="8" height="8" viewBox="0 0 10 10"><path d="m3 1 4 4-4 4" stroke="#fff" stroke-width="1.6" fill="none"/></svg></span>
    <div class="dots"><span class="on"></span><span></span><span></span></div>
  </section>

  <section class="services">
    <div class="wrap service-grid">
      <article class="service">
        <div class="service-photo" role="img" aria-label="Spray gun applying paint to a car body"></div>
        <h3>AUTOMOTIVE PAINT</h3>
        <p>Factory colour matching for every make, mixed in house and applied in our heated booth for a deep and even coat that lasts for years.</p>
        <span class="btn">READ MORE</span>
      </article>
      <article class="service">
        <div class="service-photo s2" role="img" aria-label="Panel beater shaping a car door panel"></div>
        <h3>AUTOMOTIVE PANEL</h3>
        <p>Dents, creases and rust are repaired by hand, with every panel aligned to the correct gaps before primer and colour go on.</p>
        <span class="btn">READ MORE</span>
      </article>
      <article class="service">
        <div class="service-photo s3" role="img" aria-label="Workshop floor with cars on hoists"></div>
        <h3>AUTOMOTIVE SERVICES</h3>
        <p>Bumper repairs, headlight restoration, paint protection and detailing, all handled under one roof by our own trained team.</p>
        <span class="btn">READ MORE</span>
      </article>
      <article class="service">
        <div class="service-photo s4" role="img" aria-label="Technicians working on a vehicle in the workshop"></div>
        <h3>ALL OTHER SERVICES</h3>
        <p>Fleet programs, insurance claims and custom work for private owners, with clear quotes and firm timeframes on every job.</p>
        <span class="btn">READ MORE</span>
      </article>
    </div>
  </section>

  <section class="about">
    <div class="wrap">
      <div class="about-text">
        <h2>ABOUT VELTRA PAINT &amp; PANEL</h2>
        <p>Veltra Paint &amp; Panel is a boutique Brisbane workshop repairing and refinishing all makes and models. We treat every car as if it were our own, from the first inspection to the final polish, so the result looks as good as the day it left the factory.</p>
        <p>Our team combines years of trade experience with modern colour matching tools and a clean, dust free booth. Every repair is checked under daylight lamps before handover.</p>
      </div>
      <div class="stories">
        <h2>OUR STORIES</h2>
        <div class="story">
          <div class="story-photo" role="img" aria-label="Happy customer beside her freshly painted car"></div>
          <p>A scraped door and a faded bonnet were fixed in four days. The colour match was perfect and the car now looks brand new again. Friendly staff, honest price and great service from start to finish.</p>
        </div>
      </div>
    </div>
  </section>

  <section class="works">
    <div class="wrap">
      <div class="works-text">
        <h2>VELTRA PAINT &amp; PANEL WORKS</h2>
        <p>See the difference a careful repair makes. These before and after shots show a real customer car brought back to its original shape and shine.</p>
        <p>Each job is documented so you can follow the progress at every stage.</p>
      </div>
      <div class="compare">
        <figure>
          <div class="car-photo" role="img" aria-label="Blue hatchback with damaged front before repair"></div>
          <figcaption>BEFORE</figcaption>
        </figure>
        <figure>
          <div class="car-photo after" role="img" aria-label="Same blue hatchback fully repaired and repainted"></div>
          <figcaption>AFTER</figcaption>
        </figure>
      </div>
    </div>
  </section>

  <section class="makes">
    <div class="wrap">
      <h3>ALL MODEL OF VEHICLES</h3>
      <span class="make-badge"></span><span class="make-badge"></span><span class="make-badge"></span><span class="make-badge"></span><span class="make-badge"></span><span class="make-badge"></span><span class="make-badge"></span><span class="make-badge"></span><span class="make-badge"></span>
    </div>
  </section>

  <footer class="site-footer">
    <div class="wrap">
      <div class="footer-links">
        <div><span>HOME</span><span>OUR PROCESS</span><span>PRIVATE CUSTOMERS</span><span>FLEET &amp; CORPORATE</span><span>INSURANCE</span><span>GET A QUOTE</span><span>CONNECT</span></div>
        <div>&copy; 2024 Veltra Paint &amp; Panel</div>
      </div>
      <div class="social"><span></span><span></span><span></span></div>
    </div>
  </footer>

</div>
</body>
</html>
```